Cool Website Design Gleam Shell Crew.

We need a new website, using our existing domain, with a similar function to https://www.marbeckfilm.com/ or https://www.tolvanfinishworks.com/ instagram gleam_shell.crew.
We can send google docs with pictures.
Logo attached

```html
<!DOCTYPE html>
<html lang="en">
<head>
<meta charset="utf-8">
<title>Gleam Shell Crew — Premium Vehicle Wraps &amp; Protection in Calgary</title>
<link rel="stylesheet" href="https://fonts.googleapis.com/css2?family=Plus+Jakarta+Sans:wght@600;700;800&family=Inter:wght@400;500;600;700&display=swap">
<style>
:root{
  --night:#0d0b20;
  --night-deep:#0a0616;
  --violet:#6a2ee0;
  --violet-strong:#6d28d9;
  --blue:#1f7ae8;
  --blue-bright:#1e88e5;
  --lilac:#a266ff;
  --white:#ffffff;
  --ink:#111111;
  --field:#e9e9ee;
  --field-text:#7a7a85;
  --map:#e8e8f0;
}
*{box-sizing:border-box;margin:0;padding:0}
html,body{width:1200px;height:4494px;overflow:hidden}
body{font-family:"Inter",sans-serif;color:var(--white);background:var(--white);position:relative}
.heading{font-family:"Plus Jakarta Sans",sans-serif;font-weight:800;text-transform:uppercase}
.abs{position:absolute}
.btn{position:absolute;display:flex;align-items:center;justify-content:center;font-family:"Inter",sans-serif;font-weight:700;font-size:13px;text-transform:uppercase;color:var(--white);letter-spacing:.2px}
.btn-grad{background:linear-gradient(90deg,var(--violet),var(--blue-bright))}
.btn-dark{background:var(--ink)}
.btn-outline{border:2px solid var(--white);background:transparent}
.photo{position:absolute}

/* hero */
.hero{position:absolute;left:0;top:0;width:1200px;height:668px;background:linear-gradient(160deg,#15142e 0%,#0f0d24 45%,#1a1030 100%)}
.brand{position:absolute;left:94px;top:17px;width:150px;height:70px}
.brand-name{font-family:"Plus Jakarta Sans",sans-serif;font-weight:800;font-size:17px;color:var(--lilac);text-transform:uppercase;line-height:1.05}
.brand-mark{width:22px;height:22px;background:var(--lilac);margin-top:8px}
.nav{position:absolute;top:56px;left:332px;display:flex;gap:22px;font-size:13px;font-weight:700;text-transform:uppercase}
.hero-title{position:absolute;left:94px;top:206px;font-size:44px;line-height:56px;width:560px}
.hero-title .accent{color:var(--lilac)}
.hero-sub{position:absolute;left:94px;top:402px;font-size:14px;line-height:28px;font-weight:600;text-transform:uppercase;width:560px}

/* split panels */
.panel{position:absolute;width:600px;height:551px}
.panel-blue{background:linear-gradient(135deg,#3b4de0,var(--blue-bright))}
.panel-violet{background:linear-gradient(135deg,#6a22d8,#3a4ce0)}
.panel-title{position:absolute;font-size:38px;line-height:56px}
.panel-copy{position:absolute;font-size:13px;line-height:24px;width:420px}

/* gallery */
.section-title{position:absolute;left:0;width:1200px;text-align:center;font-size:38px}
.gallery-plus{position:absolute;left:564px;top:2093px;width:70px;height:70px;border-radius:50%;background:var(--white);color:var(--ink);font-size:34px;font-weight:700;display:flex;align-items:center;justify-content:center}

/* services */
.services{position:absolute;left:0;top:2499px;width:1200px;height:738px;background:radial-gradient(ellipse at 50% 40%,#1a0b2e 0%,var(--night-deep) 70%)}
.card-title{position:absolute;width:330px;text-align:center;font-weight:700;font-size:15px;text-transform:uppercase}
.card-copy{position:absolute;width:330px;text-align:center;font-size:13px;line-height:24px}
.arrow{position:absolute;font-size:16px;font-weight:700}

/* contact */
.field{position:absolute;background:var(--field);color:var(--field-text);font-size:13px;padding:16px 18px;text-transform:uppercase}

/* stats */
.stats{position:absolute;left:188px;top:3833px;width:820px;height:248px;background:linear-gradient(90deg,#6a22d8,#1f85e6);text-align:center;z-index:2}

/* footer */
.footer{position:absolute;left:0;top:3994px;width:1200px;height:500px;background:var(--night-deep)}
.foot-col h4{font-family:"Inter",sans-serif;font-weight:700;font-size:16px;margin-bottom:16px}
.foot-col p{font-size:13px;line-height:23.7px}
.foot-col{position:absolute;top:165px}
.social{position:absolute;top:280px;width:40px;height:40px;border-radius:50%;background:var(--white)}
</style>
</head>
<body>

<section class="hero">
  <div class="brand">
    <div class="brand-name">Gleam Shell Crew</div>
    <div class="brand-mark"></div>
  </div>
  <nav class="nav"><span>Home</span><span>About</span><span>Services</span><span>Blog</span><span>Promotional Products</span><span>FAQ's</span><span>Contact</span></nav>
  <div class="btn btn-grad" style="left:989px;top:45px;width:124px;height:40px">Call Us Now</div>

  <h1 class="heading hero-title">Premium <span class="accent">Vehicle Wraps</span> &amp; Protection in Calgary</h1>
  <p class="hero-sub">Full wraps, color changes, PPF, ceramic coating &amp; fleet branding delivered with precision and style.</p>
  <div class="btn btn-grad" style="left:94px;top:487px;width:182px;height:38px">Get A Free Quote</div>

  <svg class="photo" style="left:588px;top:202px" width="602" height="393" viewBox="0 0 602 393" role="img" aria-label="Cream sport sedan at dusk, shown in slanted slices">
    <defs><linearGradient id="heroPhoto" x1="0" y1="0" x2="0" y2="1"><stop offset="0" stop-color="#3a3f2c"/><stop offset=".45" stop-color="#5c5a4a"/><stop offset=".75" stop-color="#cfc8b8"/><stop offset="1" stop-color="#2a2820"/></linearGradient></defs>
    <polygon points="112,120 190,120 100,335 0,335" fill="url(#heroPhoto)"/>
    <polygon points="262,0 310,0 200,393 150,393" fill="url(#heroPhoto)"/>
    <polygon points="350,0 478,0 440,135 602,135 540,393 240,393" fill="url(#heroPhoto)"/>
  </svg>
</section>

<div class="photo" style="left:0;top:668px;width:600px;height:551px;background:linear-gradient(180deg,#6f7c4e 0%,#c72a2a 40%,#9b1d1d 75%,#7d7a72 100%)" role="img" aria-label="Red hatchback with black racing stripes, rear view"></div>
<section class="panel panel-blue" style="left:600px;top:668px">
  <h2 class="heading panel-title" style="left:72px;top:84px">About Us</h2>
  <p class="panel-copy" style="left:72px;top:154px">Lorem ipsum dolor sit amet, consectetur adipiscing elit, sed do eiusmod tempor incididunt ut labore et dolore magna aliqua. Ut enim ad minim veniam, quis nostrud exercitation ullamco laboris nisi ut aliquip ex ea commodo consequat. Duis aute irure dolor in reprehenderit in voluptate velit esse cillum dolore eu fugiat nulla pariatur. Excepteur sint occaecat cupidatat non proident, sunt in culpa qui officia deserunt mollit anim id est laborum.</p>
  <p class="panel-copy" style="left:72px;top:334px">Lorem ipsum dolor sit amet, consectetur adipiscing elit, sed do eiusmod tempor incididunt ut labore et</p>
  <div class="btn btn-dark" style="left:72px;top:406px;width:133px;height:38px">View More</div>
</section>

<section class="panel panel-violet" style="left:0;top:1219px">
  <h2 class="heading panel-title" style="left:116px;top:88px">We Make Cars<br>Bolder</h2>
  <p class="panel-copy" style="left:116px;top:210px">Lorem ipsum dolor sit amet, consectetur adipiscing elit, sed do eiusmod tempor incididunt ut labore et dolore magna aliqua. Ut enim ad minim veniam, quis nostrud exercitation ullamco laboris nisi ut aliquip ex ea commodo consequat. Duis aute irure dolor in reprehenderit in voluptate velit esse cillum dolore eu fugiat nulla pariatur. Excepteur sint occaecat cupidatat non proident, sunt in culpa qui officia deserunt mollit anim id est laborum.</p>
  <div class="btn btn-dark" style="left:116px;top:408px;width:133px;height:38px">View More</div>
</section>
<div class="photo" style="left:600px;top:1219px;width:600px;height:553px;background:linear-gradient(180deg,#8fb4e0 0%,#d6d4cf 35%,#c8332f 60%,#8b8a84 100%)" role="img" aria-label="Red and white coupe with diagonal stripes parked by a garage"></div>

<section>
  <h2 class="heading section-title" style="top:1872px;color:var(--ink)">Our Gallery</h2>
  <div class="photo" style="left:112px;top:1948px;width:305px;height:220px;background:linear-gradient(180deg,#cfd3d6,#e9eaec 60%,#9a9c9e)" role="img" aria-label="White sedan with rear windshield lettering"></div>
  <div class="photo" style="left:112px;top:2180px;width:305px;height:220px;background:linear-gradient(180deg,#6a6a66,#4a4c4e 55%,#c9a64a)" role="img" aria-label="Matte grey hatchback with red accents in a garage"></div>
  <div class="photo" style="left:431px;top:1948px;width:338px;height:365px;background:linear-gradient(180deg,#4a4a4a,#6e6f71 55%,#2e2e2e)" role="img" aria-label="Silver sedan front three-quarter view"></div>
  <div class="gallery-plus">+</div>
  <div class="photo" style="left:778px;top:1948px;width:305px;height:220px;background:linear-gradient(180deg,#7a8a6a,#2b2fb0 55%,#6b6a62)" role="img" aria-label="Blue sedan parked outdoors"></div>
  <div class="photo" style="left:778px;top:2180px;width:305px;height:220px;background:linear-gradient(180deg,#9db7d8,#1e2436 55%,#555)" role="img" aria-label="Black sedan front view"></div>
  <div class="btn btn-grad" style="left:534px;top:2346px;width:132px;height:38px">View More</div>
</section>

<section class="services">
  <h2 class="heading section-title" style="top:110px">Our Services</h2>
  <p class="abs" style="left:330px;top:178px;width:540px;text-align:center;font-size:13px;line-height:24px">Lorem ipsum dolor sit amet, consectetur adipiscing elit, sed do eiusmod tempor incididunt ut labore et</p>
  <span class="arrow" style="left:64px;top:366px">«</span>
  <span class="arrow" style="left:1122px;top:366px">»</span>

  <div class="photo" style="left:129px;top:265px;width:286px;height:176px;background:linear-gradient(180deg,#eceff2,#d8dde0 60%,#3a3a3a)" role="img" aria-label="White fleet van with printed commercial graphics"></div>
  <div class="photo" style="left:457px;top:265px;width:286px;height:176px;background:linear-gradient(180deg,#d9d7d2,#d96a1c 55%,#4a3a2a)" role="img" aria-label="Orange sports coupe with black hood"></div>
  <div class="photo" style="left:785px;top:265px;width:286px;height:176px;background:linear-gradient(180deg,#1e3b6a,#4a6b9c 55%,#1a2c4e)" role="img" aria-label="Storefront windows with promotional graphics"></div>

  <h3 class="card-title" style="left:107px;top:476px">Printed Commercial Wraps</h3>
  <h3 class="card-title" style="left:435px;top:476px">Color Change/Custom Restyle</h3>
  <h3 class="card-title" style="left:763px;top:476px">Promotional Unlimited</h3>
  <p class="card-copy" style="left:107px;top:508px">Lorem ipsum dolor sit amet, consectetur adipiscing elit, sed do</p>
  <p class="card-copy" style="left:435px;top:508px">Lorem ipsum dolor sit amet, consectetur adipiscing elit, sed do</p>
  <p class="card-copy" style="left:763px;top:508px">Lorem ipsum dolor sit amet, consectetur adipiscing elit, sed do</p>

  <div class="btn btn-grad" style="left:127px;top:581px;width:132px;height:40px">View More</div>
  <div class="btn btn-outline" style="left:271px;top:581px;width:133px;height:40px">View Gallery</div>
  <div class="btn btn-grad" style="left:455px;top:581px;width:132px;height:40px">View More</div>
  <div class="btn btn-outline" style="left:599px;top:581px;width:133px;height:40px">View Gallery</div>
  <div class="btn btn-grad" style="left:783px;top:581px;width:132px;height:40px">View More</div>
  <div class="btn btn-outline" style="left:927px;top:581px;width:133px;height:40px">View Gallery</div>
</section>

<section>
  <div class="photo" style="left:103px;top:3341px;width:453px;height:403px;background:linear-gradient(135deg,var(--map),#d6d6e2)" role="img" aria-label="Map showing the shop location"></div>
  <h2 class="heading abs" style="left:603px;top:3368px;font-size:38px;color:var(--ink)">Contact Us</h2>
  <div class="field" style="left:603px;top:3439px;width:253px;height:49px">Name</div>
  <div class="field" style="left:868px;top:3439px;width:252px;height:49px">Phone</div>
  <div class="field" style="left:603px;top:3500px;width:517px;height:49px">Email</div>
  <div class="field" style="left:603px;top:3561px;width:517px;height:112px">Message</div>
  <div class="btn btn-grad" style="left:607px;top:3687px;width:134px;height:40px">Submit</div>
</section>

<section class="stats">
  <h2 class="heading" style="margin-top:80px;font-size:38px;text-transform:uppercase">70000 Views Per Day</h2>
  <p style="margin:16px auto 0;width:440px;font-size:13px;line-height:24px">Did you know that one car wrap can garner between 30,000 and 70,000 views per day?</p>
</section>

<footer class="footer">
  <div class="brand" style="left:112px;top:170px">
    <div class="brand-name">Gleam Shell Crew</div>
    <div class="brand-mark"></div>
  </div>
  <span class="social" style="left:112px" aria-label="Social profile"></span>
  <span class="social" style="left:160px" aria-label="Social profile"></span>
  <span class="social" style="left:211px" aria-label="Social profile"></span>
  <p class="abs" style="left:112px;top:348px;font-size:13px">Copyright@2025.All Rights Reserved</p>

  <div class="foot-col" style="left:392px">
    <h4>Services</h4>
    <p>Ceramic Coating</p><p>Color Change &amp; Custom Restyle</p><p>Printed Commercial Wraps</p><p>Promotional Unlimited</p><p>Vinyl Murals</p><p>Vinyl Graphics / Partial Wraps</p><p>Car Wraps</p><p>Signs</p>
  </div>
  <div class="foot-col" style="left:656px">
    <h4>ADDRESS</h4>
    <p>48 Kestrel Row, Unit 9, Calgary, AB</p><p>+1 (403) 555 0172</p><p>hello@gleamshellcrew.ca</p>
  </div>
  <div class="foot-col" style="left:954px">
    <h4>BUSINESS HOURS</h4>
    <p>MON – FRI: 09AM – 05PM</p><p>SAT: Appointment Only</p><p>SUN: Closed</p>
  </div>
</footer>

</body>
</html>
```